Olive Oil bottle label front and back

We need a label designed for an olive oil bottle along with a company logo. I have attached the bottle and the exact design of the bottle.

Our company is called Morvessa Crest Imports LLC but our olive oil will be called Morvessa Crest

Front - as you are looking at the bottle the handle will be to the right

Our logo
Kalamata Protected Designation of Origin stamp - if you can not find this leave a spot for it and the factory can add it
ISO certified protected designated Origin stamp - if you can not find this leave a spot for it and the factory can add it
Look Greek, simple, elegant
Look expensive
What type of oil - extra virgin, organic.

Back

Greek flag
Nutrition facts
Bar code just leave a white space for this
Website http://morvessacrestimports.example
Factory info - Kalamata, Greece
Best by date/made on date
Leave a space for company address

This link takes you to the bottle maker http://www.trendopak.example/en/proionta/ladi-ksidi/item/807-10300

Target Market(s)

We are going to be starting to sell to upscale grocery stores and specialty food stores.

Industry/Entity Type

Food Production

Requirements
Must have
• Have gold in it because of the name and logo but not shinny, old fashioned looking gold. We want more of that simple elegant looking gold.

```html
<!DOCTYPE html>
<html lang="en">
<head>
<meta charset="utf-8">
<title>Morvessa Crest – Olive Oil Front Labels</title>
<link rel="stylesheet" href="https://fonts.googleapis.com/css2?family=Cinzel:wght@500&family=Marcellus&family=Rosarivo&family=Open+Sans:wght@400;700&display=swap">
<style>
  :root {
    --page: #ffffff;
    --label-cream: #e6c99c;
    --label-kraft: #dcc49d;
    --ink: #6b4636;
    --ink-soft: #7d5a48;
    --tree-dark: #6f4a37;
    --tree-light: #a3826c;
  }
  * { box-sizing: border-box; margin: 0; padding: 0; }
  html, body { width: 880px; height: 1200px; overflow: hidden; background: var(--page); }
  .canvas { position: relative; width: 880px; height: 1200px; }

  .label { position: absolute; color: var(--ink); text-align: center; }
  .label__shape { position: absolute; left: 0; top: 0; width: 100%; height: 100%; }
  .label > *:not(.label__shape) { position: absolute; left: 0; right: 0; margin-left: auto; margin-right: auto; }

  .tree-art {
    border-radius: 50% 50% 18% 18% / 60% 60% 18% 18%;
    background: radial-gradient(ellipse at 50% 35%, var(--tree-light), var(--tree-dark) 75%);
    opacity: .85;
  }
  .brand-dot { border-radius: 50%; background: var(--ink); }
  .brand-name {
    font-family: "Cinzel", serif; font-weight: 500; color: var(--ink);
    text-transform: uppercase; line-height: 1; white-space: nowrap;
  }
  .brand-sub {
    display: flex; align-items: center; justify-content: center; gap: 6px;
    font-family: "Cinzel", serif; font-weight: 500; color: var(--ink);
    text-transform: uppercase; line-height: 1; letter-spacing: 2px; white-space: nowrap;
  }
  .brand-sub::before, .brand-sub::after { content: ""; height: 1px; background: var(--ink-soft); }
  .pressing {
    width: max-content; background: var(--ink); color: var(--label-cream);
    font-family: "Rosarivo", serif; font-weight: 700; border-radius: 10px; line-height: 1.3; white-space: nowrap;
  }
  .oil-type { font-family: "Marcellus", serif; text-transform: uppercase; color: var(--ink-soft); }
  .oil-type strong { font-family: "Rosarivo", serif; font-weight: 700; color: var(--ink); }
  .rule { height: 1px; background: var(--ink-soft); }
  .rule::after {
    content: ""; position: absolute; left: 50%; top: -3px; width: 6px; height: 6px;
    margin-left: -3px; border: 1px solid var(--ink-soft); transform: rotate(45deg); background: inherit;
  }
  .note { font-family: "Open Sans", sans-serif; color: var(--ink-soft); line-height: 1; }
  .volume { font-family: "Open Sans", sans-serif; font-weight: 700; color: var(--ink); line-height: 1; }

  /* arched front label */
  .label--arched { left: 139px; top: 424px; width: 206px; height: 634px; }
  .label--arched .tree-art { top: 26px; width: 95px; height: 84px; }
  .label--arched .brand-dot { top: 134px; width: 24px; height: 26px; }
  .label--arched .brand-name { top: 195px; font-size: 28px; letter-spacing: 2px; }
  .label--arched .brand-sub { top: 235px; font-size: 21px; }
  .label--arched .brand-sub::before, .label--arched .brand-sub::after { width: 30px; }
  .label--arched .pressing { top: 300px; font-size: 11px; padding: 1px 7px; }
  .label--arched .oil-type { top: 358px; font-size: 13.5px; line-height: 20px; }
  .label--arched .rule { top: 464px; width: 110px; }
  .label--arched .note { top: 535px; font-size: 10.5px; }
  .label--arched .volume { top: 597px; font-size: 10.5px; }

  /* medallion front label */
  .label--medallion { left: 517px; top: 430px; width: 252px; height: 586px; }
  .label--medallion .tree-art { top: 50px; width: 99px; height: 88px; }
  .label--medallion .brand-dot { top: 218px; width: 22px; height: 24px; }
  .label--medallion .brand-name { top: 273px; font-size: 28px; letter-spacing: 2px; }
  .label--medallion .brand-sub { top: 314px; font-size: 21px; }
  .label--medallion .brand-sub::before, .label--medallion .brand-sub::after { width: 28px; }
  .label--medallion .pressing { top: 409px; font-size: 9px; padding: 1px 5px; }
  .label--medallion .oil-type { top: 448px; font-size: 9.5px; line-height: 14px; }
  .label--medallion .rule { top: 487px; width: 80px; }
  .label--medallion .note { top: 514px; font-size: 6.5px; }
  .label--medallion .volume { top: 542px; font-size: 10px; }
</style>
</head>
<body>
<main class="canvas">

  <section class="label label--arched" aria-label="Front label, arched version">
    <svg class="label__shape" viewBox="0 0 206 634" aria-hidden="true">
      <path d="M0 120 C0 50 45 0 103 0 C161 0 206 50 206 120 L206 630 Q160 614 103 622 Q45 634 0 618 Z" fill="var(--label-cream)"/>
    </svg>
    <div class="tree-art" role="img" aria-label="Illustration of a gnarled olive tree"></div>
    <div class="brand-dot" aria-hidden="true"></div>
    <h1 class="brand-name">Morvessa</h1>
    <p class="brand-sub">Crest</p>
    <p class="pressing">FIRST GOLD PRESSING</p>
    <p class="oil-type">Extra virgin<br>olive oil<br>from<br><strong>KALAMATA</strong><br>region</p>
    <div class="rule" aria-hidden="true"></div>
    <p class="note">A Gluten Free Food</p>
    <p class="volume">16.9 FL OZ (500ml)</p>
  </section>

  <section class="label label--medallion" aria-label="Front label, medallion version">
    <svg class="label__shape" viewBox="0 0 252 586" aria-hidden="true">
      <circle cx="126" cy="284" r="126" fill="var(--label-kraft)"/>
      <circle cx="126" cy="284" r="119" fill="var(--page)"/>
      <path d="M55 22 Q55 12 63 10 Q70 20 126 18 Q182 20 189 10 Q197 12 197 22 L197 582 Q165 566 126 574 Q88 584 55 570 Z" fill="var(--label-kraft)"/>
      <circle cx="126" cy="284" r="113" fill="var(--label-kraft)"/>
      <circle cx="126" cy="284" r="105" fill="none" stroke="var(--ink-soft)" stroke-width="2.4" stroke-dasharray="1.5 4" stroke-linecap="round"/>
    </svg>
    <div class="tree-art" role="img" aria-label="Illustration of a gnarled olive tree"></div>
    <div class="brand-dot" aria-hidden="true"></div>
    <h2 class="brand-name">Morvessa</h2>
    <p class="brand-sub">Crest</p>
    <p class="pressing">FIRST GOLD PRESSING</p>
    <p class="oil-type">Extra virgin olive oil<br>from Kalamata region</p>
    <div class="rule" aria-hidden="true"></div>
    <p class="note">A Gluten Free Food</p>
    <p class="volume">16.9 FL OZ (500ml)</p>
  </section>

</main>
</body>
</html>
```